Business Landing Page for SEO Company

Need the landing page of the website designed - I will provide the copy, will need to include details of my company and the services offered, about us, testimonials, faq, etc., and all these elements will need to be arranged graphically on the page.

I want something similar to this: https://torvanequill.com/

Not in terms of color or theme or anything, but we offer a similar service and want to display similar information.

Th services we provide are:

Premium Links
Monthly Links Subscription
Link Insertions

Need to advertise them on the front page. Additionally need a place for testimonials, company details, etc.,

We already have logo for the website. Please use the attached file to insert the logo within the overal design.

Target Market(s)

SEO marketers and agencies

Number of Pages Required

1 page

```html
<!DOCTYPE html>
<html lang="en">
<head>
<meta charset="utf-8">
<title>Lumora – Link Building Services</title>
<link rel="stylesheet" href="https://fonts.googleapis.com/css2?family=Lato:wght@400;700;900&family=Montserrat:wght@500;600;700&display=swap">
<style>
:root{
  --blue:#2f6fe0;
  --blue-deep:#1f57d6;
  --orange:#ff6a00;
  --ink:#1d1d1d;
  --text:#3a3a3a;
  --soft:#f5f1f1;
  --lilac:#f3f2f9;
  --card:#f4efef;
  --footer:#1f1f1f;
  --white:#fff;
}
*{box-sizing:border-box;margin:0;padding:0}
html,body{width:1200px;height:4622px;overflow:hidden}
body{position:relative;background:var(--white);font-family:"Lato",sans-serif;color:var(--text)}
.abs{position:absolute}
.btn{position:absolute;display:flex;align-items:center;justify-content:center;background:var(--orange);color:var(--white);font-family:"Montserrat",sans-serif;font-weight:700;font-size:11px;border-radius:20px;letter-spacing:.3px}
.section-title{position:absolute;left:0;width:1200px;text-align:center;font-family:"Montserrat",sans-serif;font-weight:700;font-size:22px;color:var(--ink)}
.title-rule{position:absolute;left:577px;width:46px;height:3px;background:var(--blue)}

/* header */
.site-header{top:0;left:0;width:1200px;height:112px}
.brand{font-family:"Lato",sans-serif;font-weight:900;color:var(--blue);letter-spacing:-1px}
.site-header .brand{left:129px;top:20px;font-size:52px;line-height:60px}
.follow{left:648px;top:34px;font-size:10px;font-family:"Montserrat",sans-serif;color:var(--ink)}
.social-dot{top:26px;width:27px;height:27px;border-radius:50%}
.call-icon{left:888px;top:25px;width:30px;height:30px;border-radius:50%;background:var(--blue);display:flex;align-items:center;justify-content:center}
.call-label{left:933px;top:22px;font-size:11px;font-family:"Montserrat",sans-serif;color:var(--ink)}
.call-number{left:933px;top:36px;font-size:20px;font-weight:700;color:var(--ink)}
.nav{top:78px;font-family:"Montserrat",sans-serif;font-weight:500;font-size:13px;color:var(--ink)}
.nav.active{color:var(--orange);text-decoration:underline}

/* hero */
.hero{top:112px;left:0;width:1200px;height:534px;background:linear-gradient(100deg,#cfd0d2 0%,#dcdcdc 35%,#a9adb3 65%,#8e9298 100%)}
.hero-welcome{left:131px;top:157px;font-size:32px;color:var(--ink);letter-spacing:1px}
.hero-brand{left:131px;top:195px;font-size:70px;font-weight:900;color:var(--blue);letter-spacing:2px}
.hero .btn{left:136px;top:293px;width:133px;height:36px;border-radius:0;font-size:15px;font-family:"Lato",sans-serif}
.dots{left:133px;top:462px;display:flex;gap:11px;align-items:center}
.dots span{width:8px;height:8px;border-radius:50%;background:#fff}
.dots span.on{background:var(--orange);width:10px;height:10px}

/* services */
.service-card{top:777px;width:276px;height:375px;background:var(--card);border-radius:70px;text-align:center}
.service-card svg{position:absolute;left:104px;top:45px}
.service-card h3{position:absolute;top:148px;left:20px;right:20px;font-family:"Montserrat",sans-serif;font-size:14px;font-weight:700;color:var(--ink);line-height:20px}
.service-card p{position:absolute;left:44px;right:44px;font-size:13px;line-height:19px}
.service-card .btn{left:92px;width:92px;height:32px;font-size:10px}

/* about */
.about{top:1216px;left:0;width:1200px;height:465px;background:var(--soft)}
.about h2{position:absolute;left:131px;top:58px;font-family:"Montserrat",sans-serif;font-size:22px;font-weight:700;color:var(--ink)}
.about h4{position:absolute;left:131px;top:130px;width:400px;font-family:"Montserrat",sans-serif;font-size:14px;font-weight:700;color:var(--ink);line-height:22px}
.about p{position:absolute;left:131px;top:189px;width:400px;font-size:14px;line-height:21.5px}
.about .btn{left:130px;top:370px;width:104px;height:34px}
.about-photo{left:583px;top:0;width:617px;height:465px;border-top-left-radius:120px;background:linear-gradient(135deg,#3f7ef0 0%,#2c62df 50%,#1e4fcf 100%)}
.accent-bar{left:571px;top:207px;width:12px;height:263px;background:var(--orange);border-radius:0 0 8px 8px}
.accent-line{left:584px;top:1686px;width:2px;height:162px;background:var(--blue)}

/* experience */
.stat-card{width:176px;height:198px;background:var(--white);border-radius:55px;box-shadow:0 6px 22px rgba(0,0,0,.08);text-align:center;font-family:"Montserrat",sans-serif;font-size:13px;color:var(--ink);line-height:20px}
.stat-card svg{position:absolute;left:58px;top:36px}
.stat-card span{position:absolute;left:0;right:0;top:114px}
.exp-title{left:646px;top:1778px;font-family:"Montserrat",sans-serif;font-size:28px;font-weight:700;color:var(--ink);line-height:38px}
.exp-text{left:648px;top:1930px;width:395px;font-size:14px;line-height:21.5px}
.exp-btn{left:648px;top:2130px;width:188px;height:36px}

/* testimonials */
.testimonials{top:2270px;left:0;width:1200px;height:523px;background:var(--lilac)}
.quote{font-family:"Montserrat",sans-serif;font-size:52px;font-weight:700;color:var(--blue);line-height:52px}
.testimony{width:262px;font-size:14px;line-height:20.6px}
.avatar{width:40px;height:40px;border-radius:50%;background:linear-gradient(135deg,#9aa3b0,#55606e)}
.who{font-size:11px;line-height:16px;color:var(--ink)}
.who b{font-family:"Montserrat",sans-serif;font-size:10px}
.arrow{top:2554px}

/* faq */
.faq{width:452px;height:52px;border:1.5px solid #c9c9c9;border-radius:26px;display:flex;align-items:center;justify-content:space-between;padding:0 26px;font-size:12px;color:var(--ink)}

/* getting started */
.started{top:3276px;left:0;width:1200px;height:438px;background:linear-gradient(120deg,#2a63df 0%,#3a78ee 55%,#2f6be5 100%)}
.started h2{position:absolute;left:675px;top:88px;font-family:"Montserrat",sans-serif;font-size:32px;font-weight:700;color:var(--white);letter-spacing:.5px}
.started p{position:absolute;left:678px;top:146px;width:355px;font-size:17px;line-height:22.4px;color:#e6eeff}
.started .btn{left:682px;top:311px;width:140px;height:38px;font-size:14px}

/* blog */
.post{top:3852px;width:298px;height:375px;background:var(--white);box-shadow:0 4px 18px rgba(0,0,0,.08)}
.post .thumb{position:absolute;left:0;top:0;width:298px;height:161px}
.post .date{position:absolute;left:28px;top:166px;background:var(--white);padding:3px 10px;border-radius:10px;font-size:9px;color:var(--ink)}
.post h3{position:absolute;left:28px;top:201px;width:250px;font-family:"Montserrat",sans-serif;font-size:13px;font-weight:700;color:var(--ink);line-height:23px}
.post p{position:absolute;left:28px;top:256px;width:250px;font-size:11.5px;line-height:18px}
.post .btn{left:26px;top:322px;width:84px;height:26px;font-size:9px}

/* footer */
.site-footer{top:4279px;left:0;width:1200px;height:343px;background:var(--footer);color:#cfcfcf}
.site-footer .brand{left:152px;top:90px;font-size:54px;line-height:60px}
.foot-head{top:54px;font-family:"Montserrat",sans-serif;font-size:12px;font-weight:700;color:var(--white)}
.foot-menu{left:459px;top:85px;font-size:11px;line-height:19.5px}
.foot-item{font-size:11px;line-height:14px}
.ficon{width:22px;height:22px;border-radius:50%;background:var(--white);display:flex;align-items:center;justify-content:center}
.copyright{top:4584px;left:0;width:1200px;text-align:center;font-size:9px;color:#bdbdbd}
</style>
</head>
<body>

<!-- header -->
<header class="site-header abs">
  <div class="brand abs">Lumora</div>
  <div class="follow abs">FOLLOW US</div>
  <div class="social-dot abs" style="left:734px;background:#3b5bb5"></div>
  <div class="social-dot abs" style="left:768px;background:#2c8ed6"></div>
  <div class="social-dot abs" style="left:802px;background:#18305c"></div>
  <div class="social-dot abs" style="left:836px;background:#e52d27"></div>
  <div class="call-icon abs"><svg width="14" height="14" viewBox="0 0 24 24"><path fill="#fff" d="M6.6 10.8a15 15 0 0 0 6.6 6.6l2.2-2.2c.3-.3.7-.4 1-.2 1.1.4 2.3.6 3.6.6.6 0 1 .4 1 1V20c0 .6-.4 1-1 1A17 17 0 0 1 3 4c0-.6.4-1 1-1h3.5c.6 0 1 .4 1 1 0 1.3.2 2.5.6 3.6.1.3 0 .7-.2 1z"/></svg></div>
  <div class="call-label abs">CALL US NOW</div>
  <div class="call-number abs">555.014.2290</div>
  <nav>
    <a class="nav abs active" style="left:502px">HOME</a>
    <a class="nav abs" style="left:576px">ABOUT US</a>
    <a class="nav abs" style="left:680px">SERVICES</a>
    <a class="nav abs" style="left:781px">BLOG</a>
    <a class="nav abs" style="left:849px">TESTIMONIALS</a>
    <a class="nav abs" style="left:982px">CONTACT US</a>
  </nav>
</header>

<!-- hero -->
<section class="hero abs" role="img" aria-label="Hands typing on a laptop surrounded by floating digital marketing icons">
  <div class="hero-welcome abs">WELCOME TO</div>
  <div class="hero-brand abs">LUMORA</div>
  <div class="btn">READ MORE</div>
  <div class="dots abs"><span></span><span></span><span class="on"></span><span></span><span></span></div>
</section>

<!-- services -->
<h2 class="section-title" style="top:690px">OUR SERVICES</h2>
<div class="title-rule" style="top:731px"></div>

<article class="service-card abs" style="left:158px">
  <svg width="68" height="68" viewBox="0 0 68 68" fill="none" stroke-width="3">
    <path d="M22 40 L14 60 L24 56 L28 64 L34 46" stroke="var(--blue)"/>
    <path d="M46 40 L54 60 L44 56 L40 64 L34 46" stroke="var(--blue)"/>
    <circle cx="34" cy="26" r="20" stroke="var(--blue)"/>
    <circle cx="34" cy="26" r="12" stroke="var(--orange)"/>
    <path d="M34 19l2.2 4.6 5 .6-3.7 3.4 1 5-4.5-2.5-4.5 2.5 1-5-3.7-3.4 5-.6z" stroke="var(--orange)" stroke-width="2"/>
  </svg>
  <h3>PREMIUM LINKS</h3>
  <p style="top:182px">Lorem ipsum dolor sit amet consectetur adipiscing elit sed do eiusmod tempor incididunt ut labore et dolore.</p>
  <div class="btn" style="top:284px">READ MORE</div>
</article>

<article class="service-card abs" style="left:461px">
  <svg width="68" height="68" viewBox="0 0 68 68" fill="none" stroke-width="5" stroke-linecap="round">
    <rect x="28" y="6" width="18" height="34" rx="9" transform="rotate(45 37 23)" stroke="var(--blue)"/>
    <rect x="22" y="28" width="18" height="34" rx="9" transform="rotate(45 31 45)" stroke="var(--orange)"/>
  </svg>
  <h3>MONTHLY LINKS<br>SUBSCRIPTION</h3>
  <p style="top:202px">Lorem ipsum dolor sit amet consectetur adipiscing elit sed do eiusmod tempor incidid.</p>
  <div class="btn" style="top:284px">READ MORE</div>
</article>

<article class="service-card abs" style="left:766px">
  <svg width="68" height="68" viewBox="0 0 68 68" fill="none" stroke-width="2.5">
    <circle cx="34" cy="34" r="13" stroke="var(--blue)"/>
    <path d="M21 34h26M34 21c-6 8-6 18 0 26M34 21c6 8 6 18 0 26" stroke="var(--blue)"/>
    <circle cx="34" cy="7" r="4" stroke="var(--orange)"/>
    <circle cx="9" cy="30" r="4" stroke="var(--orange)"/>
    <circle cx="59" cy="30" r="4" stroke="var(--orange)"/>
    <circle cx="18" cy="56" r="4" stroke="var(--orange)"/>
    <circle cx="50" cy="56" r="4" stroke="var(--orange)"/>
    <path d="M27 10a26 26 0 0 0-14 14M41 10a26 26 0 0 1 14 14M12 38a26 26 0 0 0 4 12M56 38a26 26 0 0 1-4 12M24 60a26 26 0 0 0 20 0" stroke="var(--orange)"/>
  </svg>
  <h3>LINK INSERTIONS</h3>
  <p style="top:182px">Lorem ipsum dolor sit amet consectetur adipiscing elit sed do eiusmod tempor incididunt ut labore et dolore.</p>
  <div class="btn" style="top:284px">READ MORE</div>
</article>

<!-- about -->
<section class="about abs">
  <h2>ABOUT US</h2>
  <h4>LOREM IPSUM DOLOR SIT AMET CONSECTETUR ADIPISCING ELI&nbsp; SED DO EIUSMOD TEMPOR.</h4>
  <p>Sed ut perspiciatis unde omnis iste natus error sit volu ptatem accusantium doloremque laudantium, totam rem aperiam, eaque ipsa quae ab illo inventore veritatis et quasi architecto beatae vitae dicta sunt explicabo. Nemo enim ipsam voluptatem quia voluptas sit aspernatur aut odit aut fugit,sed quia consequuntur magni dolores eos qui ratione voluptatem sequi nesciunt.</p>
  <div class="btn">READ MORE</div>
  <div class="about-photo abs" role="img" aria-label="Team reviewing analytics charts on a laptop, tinted blue"></div>
  <div class="accent-bar abs"></div>
</section>
<div class="accent-line abs"></div>

<!-- experience -->
<div class="stat-card abs" style="left:129px;top:1749px">
  <svg width="60" height="60" viewBox="0 0 60 60" fill="none" stroke-width="3" stroke-linecap="round"><circle cx="28" cy="32" r="20" stroke="var(--blue)"/><path d="M18 30l9 9 22-24" stroke="var(--orange)"/></svg>
  <span>SPAM<br>CHECKED</span>
</div>
<div class="stat-card abs" style="left:332px;top:1774px">
  <svg width="60" height="66" viewBox="0 0 60 66" fill="none" stroke-width="2.5"><rect x="12" y="4" width="36" height="54" rx="4" stroke="var(--blue)"/><rect x="18" y="12" width="24" height="32" stroke="var(--blue)"/><circle cx="30" cy="22" r="5" stroke="var(--orange)"/><path d="M22 38v-6M28 38v-4M34 38v-8M40 38v-5" stroke="var(--orange)"/><path d="M6 40c0 10 6 22 24 22s24-12 24-22" stroke="var(--blue)"/></svg>
  <span style="top:126px">SEO<br>SUPPORT</span>
</div>
<div class="stat-card abs" style="left:129px;top:1979px">
  <svg width="60" height="60" viewBox="0 0 60 60" fill="none" stroke-width="2.5"><path d="M8 30h14l4 6h8l4-6h14v20H8z" stroke="var(--blue)"/><path d="M8 30l8-14h8M52 30l-8-14h-8" stroke="var(--blue)"/><path d="M30 32V8M22 16l8-8 8 8" stroke="var(--orange)"/></svg>
  <span style="top:118px">100,000+<br>SITE INVENTORY</span>
</div>
<div class="stat-card abs" style="left:332px;top:2004px">
  <svg width="66" height="60" viewBox="0 0 66 60" fill="none" stroke-width="2.5"><rect x="3" y="6" width="60" height="38" rx="2" stroke="var(--blue)"/><path d="M26 44v8M40 44v8M18 54h30" stroke="var(--blue)"/><rect x="10" y="14" width="10" height="22" stroke="var(--orange)"/><rect x="26" y="14" width="14" height="22" stroke="var(--orange)"/><rect x="46" y="14" width="10" height="22" stroke="var(--orange)"/></svg>
  <span style="top:118px">3-4 WEEK<br>DELIVERY</span>
</div>
<h2 class="exp-title abs">OUR UK BASED AGENCY<br>HAS YEARS OF EXPERIENCE<br>&amp; TESTING</h2>
<p class="exp-text abs">Sed ut perspiciatis unde omnis iste natus error sit volu ptatem accusantium doloremque laudantium, totam rem aperiam, eaque ipsa quae ab illo inventore veritatis et quasi architecto beatae vitae dicta sunt explicabo. Nemo enim ipsam voluptatem quia voluptas sit aspernatur aut odit aut fugit,sed quia consequuntur magni dolores eos qui ratione voluptatem sequi nesciunt.</p>
<div class="btn exp-btn">GET IN TOUCH WITH US</div>

<!-- testimonials -->
<section class="testimonials abs">
  <h2 class="section-title" style="top:55px">TESTIMONIALS</h2>
  <div class="title-rule" style="top:96px"></div>
</section>
<svg class="abs arrow" style="left:46px" width="14" height="24" viewBox="0 0 14 24"><path d="M12 2L2 12l10 10" fill="none" stroke="#b8b8c8" stroke-width="2"/></svg>
<svg class="abs arrow" style="left:1138px" width="14" height="24" viewBox="0 0 14 24"><path d="M2 2l10 10L2 22" fill="none" stroke="#b8b8c8" stroke-width="2"/></svg>

<div class="quote abs" style="left:129px;top:2414px">“</div>
<p class="testimony abs" style="left:131px;top:2464px">Lorem ipsum dolor sit amet, conse ctetur adipiscing elit, sed do eius mod tempor incididunt ut labore et dolore magna aliqua. Ut enim ad minim veniam, quis nostrud exe rcitation ullamco laboris nisi ut aliquip ex ea commodo consequat. Duis aute irure dolor in eprehen derit in voluptate velit .</p>
<div class="avatar abs" style="left:131px;top:2684px" role="img" aria-label="Client portrait"></div>
<div class="who abs" style="left:192px;top:2688px"><b>DANIEL</b><br>England</div>

<div class="quote abs" style="left:473px;top:2414px">“</div>
<p class="testimony abs" style="left:475px;top:2464px">Lorem ipsum dolor sit amet, conse ctetur adipiscing elit, sed do eius mod tempor incididunt ut labore et dolore magna aliqua. Ut enim ad minim veniam, quis nostrud exe rcitation ullamco laboris nisi ut aliquip ex ea commodo consequat. Duis aute irure dolor in eprehen derit in voluptate velit .</p>
<div class="avatar abs" style="left:475px;top:2684px" role="img" aria-label="Client portrait"></div>
<div class="who abs" style="left:535px;top:2688px"><b>DANIEL</b><br>England</div>

<div class="quote abs" style="left:823px;top:2414px">“</div>
<p class="testimony abs" style="left:825px;top:2464px">Lorem ipsum dolor sit amet, conse ctetur adipiscing elit, sed do eius mod tempor incididunt ut labore et dolore magna aliqua. Ut enim ad minim veniam, quis nostrud exe rcitation ullamco laboris nisi ut aliquip ex ea commodo consequat. Duis aute irure dolor in eprehen derit in voluptate velit .</p>
<div class="avatar abs" style="left:825px;top:2684px" role="img" aria-label="Client portrait"></div>
<div class="who abs" style="left:884px;top:2688px"><b>DANIEL</b><br>England</div>

<!-- faq -->
<h2 class="section-title" style="top:2843px">FAQ</h2>
<div class="title-rule" style="top:2884px"></div>
<div class="faq abs" style="left:138px;top:2936px">Lorem ipsum dolor sit amet&nbsp; conse ctetur adipiscing elit?<svg width="12" height="8" viewBox="0 0 12 8"><path d="M1 1l5 5 5-5" fill="none" stroke="#555" stroke-width="1.5"/></svg></div>
<div class="faq abs" style="left:605px;top:2936px">Lorem ipsum dolor sit amet&nbsp; conse ctetur adipiscing elit?<svg width="12" height="8" viewBox="0 0 12 8"><path d="M1 1l5 5 5-5" fill="none" stroke="#555" stroke-width="1.5"/></svg></div>
<div class="faq abs" style="left:138px;top:3008px">But I must explain to you how all this mistaken idea?<svg width="12" height="8" viewBox="0 0 12 8"><path d="M1 1l5 5 5-5" fill="none" stroke="#555" stroke-width="1.5"/></svg></div>
<div class="faq abs" style="left:605px;top:3008px">At vero eos et accusamus et iusto odio dignissimos du?<svg width="12" height="8" viewBox="0 0 12 8"><path d="M1 1l5 5 5-5" fill="none" stroke="#555" stroke-width="1.5"/></svg></div>
<div class="faq abs" style="left:138px;top:3081px">Lorem ipsum dolor sit amet&nbsp; conse ctetur adipiscing elit?<svg width="12" height="8" viewBox="0 0 12 8"><path d="M1 1l5 5 5-5" fill="none" stroke="#555" stroke-width="1.5"/></svg></div>
<div class="faq abs" style="left:605px;top:3081px">On the other hand, we denounce with righteous indign?<svg width="12" height="8" viewBox="0 0 12 8"><path d="M1 1l5 5 5-5" fill="none" stroke="#555" stroke-width="1.5"/></svg></div>
<div class="btn" style="left:524px;top:3164px;width:149px;height:34px;font-size:11px">VIEW MORE FAQS</div>

<!-- getting started -->
<section class="started abs" role="img" aria-label="Person typing on a laptop at a desk, tinted blue">
  <h2>GETTING STARTED</h2>
  <p>Lorem ipsum dolor sit amet, conse ctetur adipiscing elit, sed do eius mod tempor incididunt ut labore et dolore magna aliqua. Ut enim ad minim veniam, quis nostrud exe rcitation ullamco laboris nisi ut aliquip ex ea commodo consequat.</p>
  <div class="btn">CONTACT US</div>
</section>

<!-- blog -->
<h2 class="section-title" style="top:3763px">LATEST BLOG</h2>
<div class="title-rule" style="top:3804px"></div>

<article class="post abs" style="left:129px">
  <div class="thumb" role="img" aria-label="Person working on a laptop holding a phone" style="background:linear-gradient(135deg,#c9ccd0,#7d848c)"></div>
  <span class="date">13 Jan,2020</span>
  <h3>LOREM IPSUM DOLOR SIT AMET CONSECTETUR ADIPISCIN.</h3>
  <p>Lorem ipsum dolor sit amet, conse ctetur adipiscing elit, sed do eius mod tempor incididunt ut labore et dolor.</p>
  <div class="btn">READ MORE</div>
</article>
<article class="post abs" style="left:450px">
  <div class="thumb" role="img" aria-label="Hands typing on a laptop beside a plant" style="background:linear-gradient(135deg,#e3e0d6,#8c8a7e)"></div>
  <span class="date">13 Jan,2020</span>
  <h3>LOREM IPSUM DOLOR SIT AMET CONSECTETUR ADIPISCIN.</h3>
  <p>Lorem ipsum dolor sit amet, conse ctetur adipiscing elit, sed do eius mod tempor incididunt ut labore et dolor.</p>
  <div class="btn">READ MORE</div>
</article>
<article class="post abs" style="left:770px">
  <div class="thumb" role="img" aria-label="Woman working on a laptop by a window" style="background:linear-gradient(135deg,#eceae6,#a7a39b)"></div>
  <span class="date">13 Jan,2020</span>
  <h3>LOREM IPSUM DOLOR SIT AMET CONSECTETUR ADIPISCIN.</h3>
  <p>Lorem ipsum dolor sit amet, conse ctetur adipiscing elit, sed do eius mod tempor incididunt ut labore et dolor.</p>
  <div class="btn">READ MORE</div>
</article>

<!-- footer -->
<footer class="site-footer abs">
  <div class="brand abs">Lumora</div>
  <div class="foot-head abs" style="left:459px">MENU</div>
  <div class="foot-menu abs">HOME<br>ABOUT US<br>SERVICES<br>BLOG<br>TESTIMONIALS<br>CONTACT US</div>

  <div class="foot-head abs" style="left:660px">CONTACT US</div>
  <div class="ficon abs" style="left:660px;top:89px"><svg width="10" height="12" viewBox="0 0 10 12"><path d="M5 0a4 4 0 0 1 4 4c0 3-4 8-4 8S1 7 1 4a4 4 0 0 1 4-4z" fill="#1f1f1f"/><circle cx="5" cy="4" r="1.5" fill="#fff"/></svg></div>
  <div class="foot-item abs" style="left:692px;top:88px">2715 Harlow Street<br>Eastvale, CA 91752</div>
  <div class="ficon abs" style="left:660px;top:142px"><svg width="11" height="11" viewBox="0 0 24 24"><path fill="#1f1f1f" d="M6.6 10.8a15 15 0 0 0 6.6 6.6l2.2-2.2c.3-.3.7-.4 1-.2 1.1.4 2.3.6 3.6.6.6 0 1 .4 1 1V20c0 .6-.4 1-1 1A17 17 0 0 1 3 4c0-.6.4-1 1-1h3.5c.6 0 1 .4 1 1 0 1.3.2 2.5.6 3.6.1.3 0 .7-.2 1z"/></svg></div>
  <div class="foot-item abs" style="left:692px;top:141px">Call Us<br>555.014.2290</div>
  <div class="ficon abs" style="left:660px;top:190px"><svg width="11" height="9" viewBox="0 0 11 9"><rect x=".5" y=".5" width="10" height="8" fill="#1f1f1f"/><path d="M.5 .5l5 4 5-4" fill="none" stroke="#fff"/></svg></div>
  <div class="foot-item abs" style="left:692px;top:189px">E mail Us<br>info@lumora.com</div>

  <div class="foot-head abs" style="left:953px">FOLLOW US</div>
  <div class="ficon abs" style="left:951px;top:80px"></div>
  <div class="foot-item abs" style="left:986px;top:79px">Like us on<br>FRIENDLOOP</div>
  <div class="ficon abs" style="left:951px;top:132px"></div>
  <div class="foot-item abs" style="left:986px;top:131px">Follow us on<br>CHIRPLINE</div>
  <div class="ficon abs" style="left:951px;top:184px"></div>
  <div class="foot-item abs" style="left:986px;top:183px">Follow us on<br>WORKMESH</div>
</footer>
<div class="copyright abs">Copyright © 2021 All Rights Reserved</div>

</body>
</html>
```